Veldmark Supplies Business Card

Professional business card that stand out to our potential customers. Front and back with clean modern design

Industry/Entity Type

Oil and gas

Contact Information for Business Card

Name, address, website , office phone and cell number

Requirements
Must have
• Editable files for each employee

```html
<!DOCTYPE html>
<html lang="en">
<head>
<meta charset="utf-8">
<title>Veldmark Supplies Business Card</title>
<link href="https://fonts.googleapis.com/css2?family=Montserrat:wght@400;500;700&display=swap" rel="stylesheet">
<style>
  :root {
    --page: #e9e8ea;
    --card-white: #ffffff;
    --brand-red: #e8262b;
    --brand-blue: #08b0d2;
    --brand-blue-deep: #0a8fae;
    --ink: #1c1c1c;
  }
  * { margin: 0; padding: 0; box-sizing: border-box; }
  html, body {
    width: 1200px; height: 1108px; overflow: hidden;
    background: var(--page);
    font-family: "Montserrat", sans-serif;
  }
  .card {
    position: absolute;
    left: 219px; width: 774px;
  }
  .card-front { top: 50px; height: 472px; background: var(--card-white); }
  .card-back { top: 568px; height: 455px; background: var(--brand-blue); }

  .brand-block {
    position: absolute; left: 106px; top: 170px; width: 256px;
    display: flex; flex-direction: column; align-items: center; gap: 22px;
  }
  .brand-square { width: 70px; height: 70px; background: var(--brand-red); }
  .brand-name {
    font-weight: 700; font-size: 20px; letter-spacing: 0.5px;
    color: var(--brand-red); text-transform: uppercase; white-space: nowrap;
  }

  .divider {
    position: absolute; left: 380px; top: 142px;
    width: 2px; height: 190px; background: var(--brand-red);
  }

  .person { position: absolute; left: 400px; top: 138px; }
  .person-name { font-weight: 700; font-size: 29px; color: var(--brand-red); line-height: 1.15; }
  .person-title { font-size: 17px; color: var(--ink); margin-top: 2px; }

  .contact-list { list-style: none; position: absolute; left: 400px; top: 220px; }
  .contact-list li {
    display: flex; align-items: center; gap: 8px;
    font-size: 17px; color: var(--ink); height: 30px;
  }
  .contact-list svg { width: 16px; height: 16px; flex: none; fill: var(--brand-blue); }

  .address {
    position: absolute; left: 0; right: 0; top: 396px;
    text-align: center; font-size: 17px; color: var(--ink);
  }

  .back-brand {
    position: absolute; left: 0; right: 0; top: 150px;
    display: flex; flex-direction: column; align-items: center; gap: 40px;
  }
  .back-square { width: 130px; height: 130px; background: var(--brand-blue-deep); }
  .back-name {
    font-weight: 700; font-size: 34px; letter-spacing: 1px;
    color: var(--brand-blue-deep); text-transform: uppercase;
  }
</style>
</head>
<body>
  <section class="card card-front">
    <div class="brand-block">
      <div class="brand-square"></div>
      <div class="brand-name">Veldmark Supplies</div>
    </div>
    <div class="divider"></div>
    <div class="person">
      <div class="person-name">Tarek Almasri</div>
      <div class="person-title">President</div>
    </div>
    <ul class="contact-list">
      <li><svg viewBox="0 0 16 16"><path d="M1 5c0-2 3-3 7-3s7 1 7 3v1h-4V5H5v1H1zM3 7h10l1 7H2zM8 9a2 2 0 1 0 0 4 2 2 0 0 0 0-4z"/></svg>+1.555.210.0400 x123</li>
      <li><svg viewBox="0 0 16 16"><path d="M3 1l3 3-2 2c1 2 3 4 5 5l2-2 3 3-2 3C6 14 1 9 1 3z"/></svg>+1.555.318.772</li>
      <li><svg viewBox="0 0 16 16"><path d="M1 4h14v1L8 9 1 5zM1 6.5l7 4 7-4V13H1z"/></svg>info@veldmarksupplies.com</li>
      <li><svg viewBox="0 0 16 16"><path d="M8 1a7 7 0 1 0 0 14A7 7 0 0 0 8 1zM4 5l3 1 1 3-2 1 1 3-3-2V7zm6-2l2 2-1 3-2-1z"/></svg>www.veldmarksupplies.com</li>
    </ul>
    <p class="address">48 Foundry Court Ashbury, NJ 07000 USA</p>
  </section>

  <section class="card card-back">
    <div class="back-brand">
      <div class="back-square"></div>
      <div class="back-name">Veldmark Supplies</div>
    </div>
  </section>
</body>
</html>
```